​Silver Harbor Rhythm provides personal, friendly service in a fun and high energy environment. We are based in Vermont.

We would like a card that appeals to a wide range of audiences as we do a wide range of events. Please feel free to check out our website silverharborrhythm.net for inspiration.

Target Market(s)

weddings, corporate, birthday parties, colleges

Industry/Entity Type

Business

Contact Information for Business Card

Silver Harbor Rhythm
Providing Entertainment For All Occasions
555 274 9160
silverharborrhythm@mailnest.net
silverharborrhythm.net

```html
<!DOCTYPE html>
<html lang="en">
<head>
<meta charset="utf-8">
<title>Silver Harbor Rhythm – Business Card</title>
<link href="https://fonts.googleapis.com/css2?family=Open+Sans:wght@400;600;700&display=swap" rel="stylesheet">
<style>
  :root {
    --forest: #2e5b12;
    --forest-dark: #244a0d;
    --paper: #ffffff;
    --ink: #3a3a3a;
    --muted: #6b6b6b;
    --rule: #d6d6d6;
    --backdrop: #e9e6e1;
  }
  * { margin: 0; padding: 0; box-sizing: border-box; }
  html, body {
    width: 1200px;
    height: 829px;
    overflow: hidden;
    background: var(--backdrop);
    font-family: "Open Sans", Arial, sans-serif;
  }
  .stage {
    position: relative;
    width: 1200px;
    height: 829px;
  }
  .card {
    position: absolute;
    top: 266px;
    width: 520px;
    height: 297px;
    overflow: hidden;
    box-shadow: 0 6px 18px rgba(0,0,0,0.18);
  }

  /* Front */
  .card-front {
    left: 50px;
    background: var(--paper);
  }
  .tab {
    position: absolute;
    background: var(--forest);
  }
  .tab-top-right {
    top: 0;
    right: 0;
    width: 150px;
    height: 12px;
    border-bottom-left-radius: 12px;
  }
  .tab-right-edge {
    top: 0;
    right: 0;
    width: 12px;
    height: 120px;
    border-bottom-left-radius: 12px;
  }
  .tab-bottom-left {
    bottom: 0;
    left: 0;
    width: 150px;
    height: 12px;
    border-top-right-radius: 12px;
  }
  .tab-left-edge {
    bottom: 0;
    left: 0;
    width: 12px;
    height: 120px;
    border-top-right-radius: 12px;
  }
  .brand {
    position: absolute;
    left: 38px;
    top: 120px;
    width: 250px;
    display: flex;
    align-items: center;
    gap: 10px;
  }
  .brand-mark {
    width: 14px;
    height: 14px;
    background: var(--forest);
    flex: none;
  }
  .brand-name {
    font-weight: 700;
    font-size: 22px;
    line-height: 1.1;
    color: var(--forest);
    text-transform: uppercase;
    letter-spacing: 0.5px;
  }
  .divider {
    position: absolute;
    left: 300px;
    top: 40px;
    width: 1px;
    height: 200px;
    background: var(--rule);
    box-shadow: 2px 0 4px rgba(0,0,0,0.08);
  }
  .contact {
    position: absolute;
    left: 318px;
    top: 44px;
    right: 20px;
    color: var(--ink);
  }
  .person-name {
    font-weight: 700;
    font-size: 15px;
    color: var(--forest);
    line-height: 1.2;
  }
  .person-title {
    font-weight: 600;
    font-size: 12px;
    color: var(--ink);
    margin-bottom: 8px;
  }
  .contact-line {
    display: flex;
    align-items: center;
    gap: 6px;
    font-size: 10.5px;
    line-height: 1.9;
    white-space: nowrap;
  }
  .contact-line svg { flex: none; }
  .address {
    margin-top: 8px;
    font-size: 10.5px;
    line-height: 1.7;
    color: var(--muted);
  }

  /* Back */
  .card-back {
    left: 630px;
    background: var(--forest);
  }
  .back-name {
    position: absolute;
    left: 0;
    right: 0;
    top: 100px;
    text-align: center;
    font-weight: 700;
    font-size: 32px;
    color: var(--paper);
    text-transform: uppercase;
    letter-spacing: 1px;
  }
  .back-url {
    position: absolute;
    right: 28px;
    bottom: 26px;
    font-size: 15px;
    color: var(--paper);
    letter-spacing: 0.5px;
  }
</style>
</head>
<body>
<main class="stage">

  <section class="card card-front" aria-label="Card front">
    <span class="tab tab-top-right"></span>
    <span class="tab tab-right-edge"></span>
    <span class="tab tab-bottom-left"></span>
    <span class="tab tab-left-edge"></span>

    <div class="brand">
      <span class="brand-mark"></span>
      <span class="brand-name">Silver Harbor Rhythm</span>
    </div>

    <div class="divider"></div>

    <div class="contact">
      <p class="person-name">Your Name</p>
      <p class="person-title">Title</p>
      <p class="contact-line">
        <svg width="11" height="11" viewBox="0 0 12 12" aria-hidden="true">
          <circle cx="6" cy="6" r="6" fill="var(--forest)"/>
          <path d="M4 3.2l1 1.6-.6.7c.4.9 1 1.5 1.9 1.9l.7-.6 1.6 1-.5 1.1C6 8.8 3.2 6 3 3.7z" fill="#fff"/>
        </svg>
        555 274 9160
      </p>
      <p class="contact-line">
        <svg width="11" height="11" viewBox="0 0 12 12" aria-hidden="true">
          <circle cx="6" cy="6" r="6" fill="var(--forest)"/>
          <rect x="3" y="4" width="6" height="4" fill="#fff"/>
          <path d="M3 4l3 2.2L9 4" stroke="var(--forest)" stroke-width="0.7" fill="none"/>
        </svg>
        silverharborrhythm@mailnest.net
      </p>
      <p class="contact-line">
        <svg width="11" height="11" viewBox="0 0 12 12" aria-hidden="true">
          <circle cx="6" cy="6" r="6" fill="var(--forest)"/>
          <circle cx="6" cy="6" r="3" fill="none" stroke="#fff" stroke-width="0.8"/>
          <path d="M3 6h6M6 3v6" stroke="#fff" stroke-width="0.7"/>
        </svg>
        www.silverharborrhythm.net
      </p>
      <p class="address">Street Name, City Name<br>Zip Code-00000</p>
    </div>
  </section>

  <section class="card card-back" aria-label="Card back">
    <p class="back-name">Silver Harbor Rhythm</p>
    <p class="back-url">www.silverharborrhythm.net</p>
  </section>

</main>
</body>
</html>
```